Marlow Sail Works President Business Card Carbon fiber catamarans

Hi.. I need a new business card design.. I am the President of a high tech yacht builder. We build Carbon Fiber go fast catamarans... Maybe we use the file I am sharing to you as the back of the card.. We need to look cool and crisp ...

Target Market(s)

Affluent People who will purchase a cool yacht

Industry/Entity Type

Custom Yacht Builder

Contact Information for Business Card

Dean Pellway , President, 731.508.2164 USA

Font styles to use
Serif

Requirements
Must have
• the clean crisp cool feel
Nice to have
• clean and crisp
Should not have
• Bold ugly

```html
<!DOCTYPE html>
<html lang="en">
<head>
<meta charset="utf-8">
<title>Marlow Sail Works — Business Card</title>
<link href="https://fonts.googleapis.com/css2?family=Michroma&family=Nunito+Sans:wght@400&display=swap" rel="stylesheet">
<style>
  :root {
    --page: #1b1b1c;
    --card-dark: #0b0b0c;
    --card-mid: #1a1a1b;
    --silver: #d9d9d9;
    --silver-soft: #bdbdbd;
    --edge: #e6e6e6;
    --divider: #3a3a3c;
  }
  * { margin: 0; padding: 0; box-sizing: border-box; }
  html, body {
    width: 1200px; height: 1015px; overflow: hidden;
    background: radial-gradient(ellipse at 50% 40%, #2a2a2b 0%, var(--page) 70%);
  }
  .canvas { position: relative; width: 1200px; height: 1015px; }

  .card {
    position: absolute;
    width: 560px; height: 320px;
    box-shadow: 0 18px 40px rgba(0,0,0,.6);
    overflow: hidden;
  }
  .card--front { left: 90px; top: 130px; }
  .card--back  { left: 550px; top: 560px; }

  .card__surface {
    position: absolute; inset: 0 0 8px 0;
    background: linear-gradient(135deg, var(--card-mid) 0%, var(--card-dark) 55%, #141415 100%);
  }
  .card__edge {
    position: absolute; left: 0; right: 0; bottom: 0; height: 8px;
    background: var(--edge);
  }

  .brand {
    position: absolute;
    display: flex; align-items: center; gap: 14px;
    font-family: "Michroma", sans-serif;
    color: var(--silver);
    letter-spacing: 4px;
    white-space: nowrap;
  }
  .brand__dot {
    width: 30px; height: 30px; border-radius: 50%;
    background: var(--silver);
    flex: none;
  }
  .card--front .brand { left: 0; right: 0; top: 140px; justify-content: center; font-size: 24px; }

  .card--back .brand {
    left: 26px; width: 262px; top: 162px;
    font-size: 12px; letter-spacing: 1.5px; gap: 8px;
  }
  .card--back .brand__dot { width: 18px; height: 18px; }

  .divider {
    position: absolute; left: 310px; top: 0; bottom: 8px; width: 1px;
    background: var(--divider);
  }

  .contact {
    position: absolute; left: 332px; top: 58px; right: 16px;
    color: var(--silver);
    font-family: "Nunito Sans", sans-serif;
  }
  .contact__name {
    font-family: "Michroma", sans-serif;
    font-size: 15px; letter-spacing: 2px;
    color: var(--silver);
    white-space: nowrap;
  }
  .contact__title { font-size: 15px; margin-top: 2px; color: var(--silver-soft); }
  .contact__list { list-style: none; margin-top: 18px; }
  .contact__item {
    display: flex; align-items: center; gap: 8px;
    font-size: 14px; line-height: 22px; white-space: nowrap;
  }
  .contact__item--address { margin-top: 16px; }
  .icon { width: 13px; height: 13px; flex: none; fill: none; stroke: var(--silver); stroke-width: 1.6; }
  .icon--solid { fill: var(--silver); stroke: none; }
</style>
</head>
<body>
<div class="canvas">

  <section class="card card--front">
    <div class="card__surface" role="img" aria-label="Black carbon fibre weave texture"></div>
    <div class="brand"><span class="brand__dot"></span>MARLOW SAIL WORKS</div>
    <div class="card__edge"></div>
  </section>

  <section class="card card--back">
    <div class="card__surface" role="img" aria-label="Black carbon fibre weave texture"></div>
    <div class="brand"><span class="brand__dot"></span>MARLOW SAIL WORKS</div>
    <div class="divider"></div>
    <div class="contact">
      <p class="contact__name">DEAN PELLWAY</p>
      <p class="contact__title">President</p>
      <ul class="contact__list">
        <li class="contact__item">
          <svg class="icon" viewBox="0 0 16 16"><path d="M4 2l2.5 3-1.5 1.5c1 2 2.5 3.5 4.5 4.5L11 9.5l3 2.5-1.5 2C7 14 2 9 2 3.5z"/></svg>
          731.508.2164
        </li>
        <li class="contact__item">
          <svg class="icon" viewBox="0 0 16 16"><rect x="1.5" y="3.5" width="13" height="9"/><path d="M1.5 3.5L8 9l6.5-5.5"/></svg>
          info@marlowsail.com
        </li>
        <li class="contact__item">
          <svg class="icon" viewBox="0 0 16 16"><circle cx="8" cy="8" r="6.5"/><ellipse cx="8" cy="8" rx="3" ry="6.5"/><path d="M1.5 8h13"/></svg>
          www.marlowsailworks.com
        </li>
        <li class="contact__item contact__item--address">
          <svg class="icon icon--solid" viewBox="0 0 16 16"><path d="M8 1a5 5 0 0 0-5 5c0 3.8 5 9 5 9s5-5.2 5-9a5 5 0 0 0-5-5zm0 7a2 2 0 1 1 0-4 2 2 0 0 1 0 4z"/></svg>
          Rhode Island 02840, USA
        </li>
      </ul>
    </div>
    <div class="card__edge"></div>
  </section>

</div>
</body>
</html>
```